Life Coaching and Personal Development Business. Needs Business Card with Logo

We are a Life Coaching and Personal Development Business based in Melbourne, Victoria. We specialise in assisting Individuals who find themselves at cross roads due to career, relationships or just life experiences that are preventing them from having extraordinary lives in happiness, finance or relationships or just being disconnected from a sense of purpose. Our motto is "we help you get there".

Reason: I am awaiting final concepts from a couple of designers

Reason: Deadline passed so now would like to see more options.

Target Market(s)

Individuals who want to move through the cross roads and who are aware that they require help to do so. They are seeking happy, for filing lives through all aspects career, relationships, family and finance

Industry/Entity Type

Finance

Font styles to use
Script

Requirements
Must have
• logo which is representative of moving forward
Business Name: RD Maple Harbour
ABN: 5038617294

I do not have a preference with colour but I do not want red orange or green

Should not have
• The card must not be to busy.

```html
<!DOCTYPE html>
<html lang="en">
<head>
<meta charset="utf-8">
<title>RD Maple Harbour – Business Card</title>
<link rel="stylesheet" href="https://fonts.googleapis.com/css2?family=Lato:wght@400;700&family=Dancing+Script:wght@600&display=swap">
<style>
  :root {
    --bg: #ecebe8;
    --card: #ffffff;
    --card-shade: #f3f3f3;
    --ink: #3a3a3a;
    --frame: #333333;
    --yellow: #f4d35e;
    --violet: #7f8fd8;
    --teal: #2fb3c7;
    --white: #ffffff;
  }
  * { box-sizing: border-box; margin: 0; padding: 0; }
  html, body {
    width: 1200px; height: 1024px; overflow: hidden;
    background: var(--bg);
    font-family: "Lato", Arial, sans-serif;
  }
  .canvas {
    position: relative; width: 1200px; height: 1024px;
    display: flex; justify-content: center; align-items: center; gap: 80px;
  }
  .card {
    position: relative; width: 420px; height: 720px;
    background: linear-gradient(180deg, var(--card) 0%, var(--card-shade) 100%);
    box-shadow: 0 10px 30px rgba(0,0,0,.15);
    overflow: hidden;
  }

  /* Front */
  .front__head {
    height: 400px; display: flex; flex-direction: column;
    align-items: center; justify-content: center; gap: 34px;
  }
  .portrait-frame {
    width: 150px; height: 130px; border: 10px solid var(--frame);
    padding: 14px;
  }
  .portrait-frame__fill {
    width: 100%; height: 100%;
    background: linear-gradient(180deg, #eeeeee 0%, #d6d6d6 100%);
  }
  .holder-name {
    font-size: 40px; font-weight: 700; color: var(--ink); letter-spacing: .5px;
  }
  .contact-band {
    height: 106.66px; display: flex; flex-direction: column;
    align-items: center; justify-content: center; gap: 10px;
    color: var(--white); font-size: 18px; letter-spacing: .3px;
    white-space: nowrap;
  }
  .contact-band svg { width: 22px; height: 22px; fill: var(--white); }
  .contact-band--address { background: var(--yellow); }
  .contact-band--phone { background: var(--violet); }
  .contact-band--email { background: var(--teal); }

  /* Back */
  .back__edge {
    position: absolute; top: 0; bottom: 0; width: 16px;
    display: flex; flex-direction: column;
  }
  .back__edge--left { left: 0; }
  .back__edge--right { right: 0; }
  .back__edge span { display: block; }
  .edge-violet { background: var(--violet); flex: 1; }
  .edge-yellow { background: var(--yellow); flex: 4; }
  .edge-teal { background: var(--teal); flex: 1; }
  .back__body {
    position: absolute; inset: 0;
    display: flex; flex-direction: column; align-items: center; justify-content: center;
    gap: 40px;
  }
  .brand {
    display: flex; align-items: center; gap: 12px;
    font-size: 26px; font-weight: 700; color: var(--ink); letter-spacing: .5px;
  }
  .brand__dot {
    width: 18px; height: 18px; border-radius: 50%; background: var(--teal);
  }
  .motto {
    display: flex; align-items: center;
    font-family: "Dancing Script", "Brush Script MT", cursive;
    font-size: 40px; font-weight: 600; color: var(--ink);
  }
  .motto__mark {
    font-family: "Lato", Arial, sans-serif;
    color: var(--teal); font-weight: 700; font-size: 44px;
    line-height: 0; margin: 0 8px; position: relative; top: 4px;
  }
</style>
</head>
<body>
<main class="canvas">

  <section class="card front" aria-label="Card front">
    <div class="front__head">
      <div class="portrait-frame">
        <div class="portrait-frame__fill" role="img" aria-label="Portrait photo of the coach"></div>
      </div>
      <h1 class="holder-name">Clara Whitfield</h1>
    </div>

    <div class="contact-band contact-band--address">
      <svg viewBox="0 0 24 24" aria-hidden="true"><path d="M12 2a7 7 0 0 0-7 7c0 5.2 7 13 7 13s7-7.8 7-13a7 7 0 0 0-7-7zm0 9.5A2.5 2.5 0 1 1 12 6.5a2.5 2.5 0 0 1 0 5z"/></svg>
      <span>Add: P.O. Box 4162, Elsternwick VIC 3185</span>
    </div>
    <div class="contact-band contact-band--phone">
      <svg viewBox="0 0 24 24" aria-hidden="true"><path d="M6.6 10.8a15.1 15.1 0 0 0 6.6 6.6l2.2-2.2a1 1 0 0 1 1-.25 11.4 11.4 0 0 0 3.6.57 1 1 0 0 1 1 1V20a1 1 0 0 1-1 1A17 17 0 0 1 3 4a1 1 0 0 1 1-1h3.5a1 1 0 0 1 1 1c0 1.25.2 2.45.57 3.6a1 1 0 0 1-.25 1z"/></svg>
      <span>5038 617 294</span>
    </div>
    <div class="contact-band contact-band--email">
      <svg viewBox="0 0 24 24" aria-hidden="true"><path d="M2 5h20v14H2z M2 5l10 8 10-8" fill="none" stroke="#ffffff" stroke-width="2" stroke-linejoin="round"/></svg>
      <span>clara@rdmapleharbour.com.au</span>
    </div>
  </section>

  <section class="card back" aria-label="Card back">
    <div class="back__edge back__edge--left">
      <span class="edge-yellow"></span>
      <span class="edge-teal"></span>
    </div>
    <div class="back__edge back__edge--right">
      <span class="edge-violet"></span>
      <span class="edge-yellow"></span>
    </div>
    <div class="back__body">
      <p class="brand"><span class="brand__dot" aria-hidden="true"></span>RD Maple Harbour</p>
      <p class="motto"><span class="motto__mark">“</span>we help you get there<span class="motto__mark">”</span></p>
    </div>
  </section>

</main>
</body>
</html>
```